Custom Cabinet Shop Needs a website design

Hi,
We need a website for a Custom Cabinet Shop and Cabinet parts manufacturing business.
The business has two sides to it. One side provides custom Kitchens, vanities, entertainment units, offices and what not to homeowners and contractors.
The 2nd side of the business provides built to order cabinet boxes and other parts required to put together a project to other cabinet shops, small contractors looking to install there own cabinets.
Website will need a Gallery to display work.
Color scheme to go well with logo.
current website is www.brambleoakcustomcabinets.com
being changed to www.brambleoak.ca
Logo Included in attached files.
Tagline "Joinery with Spirit"
Mission Statement "Our passion is to deliver inspired cabinetry solutions to suit all your needs, supported by our phenomenal star class customer service"
The website should convey quality and professionalism.
Thank you.
Homeowners/ Contractors
Entertainment

```html
<!DOCTYPE html>
<html lang="en">
<head>
<meta charset="utf-8">
<title>Bramble Oak Custom Cabinets</title>
<link href="https://fonts.googleapis.com/css2?family=Source+Sans+3:ital,wght@0,400;0,600;0,700;1,400;1,600&display=swap" rel="stylesheet">
<style>
:root{
  --ink:#4a4a4a;
  --body:#5a5a5a;
  --wood:#c8783e;
  --wood-light:#e3a065;
  --wood-dark:#a45a26;
  --accent:#ef6329;
  --rule:#e2e2e2;
  --footer:#595959;
  --footer-field:#444;
  --footer-text:#d9d9d9;
  --white:#fff;
}
*{margin:0;padding:0;box-sizing:border-box}
html,body{width:720px;height:1200px;overflow:hidden;background:var(--white)}
body{position:relative;font-family:"Source Sans 3",Arial,sans-serif;color:var(--ink)}
.abs{position:absolute}

/* header */
.brand{left:108px;top:36px;display:flex;align-items:center;gap:8px}
.brand-mark{width:22px;height:22px;background:var(--accent)}
.brand-name{font-size:15px;font-weight:700;color:#222;letter-spacing:.5px}
.nav{left:354px;top:26px;width:262px;height:48px}
.nav-item{position:absolute;top:0;width:38px;height:36px;border:1px solid #dcdcdc;border-radius:4px;background:#f8f8f8;font-size:5.5px;color:#666;text-align:center;line-height:36px}
.nav-shelf{position:absolute;left:0;top:40px;width:262px;height:5px;background:var(--wood);box-shadow:0 3px 4px rgba(0,0,0,.18)}

/* hero */
.hero{left:104px;top:94px;width:512px;height:180px}
.hero-top,.hero-bottom{position:absolute;left:0;width:512px;height:7px;background:var(--wood);box-shadow:0 2px 3px rgba(0,0,0,.2)}
.hero-top{top:0}.hero-bottom{top:168px}
.hero-frame{position:absolute;left:24px;top:7px;width:468px;height:161px;background:linear-gradient(180deg,var(--wood-light),var(--wood))}
.hero-photo{position:absolute;left:28px;top:12px;width:304px;height:146px;background:linear-gradient(180deg,#e9e6e1 0%,#f4f2ee 45%,#e2dcd2 62%,#c9b48f 85%,#b99e74 100%)}
.hero-arrow{position:absolute;top:52px;width:16px;height:44px;background:rgba(255,255,255,.8);font-size:20px;color:#888;text-align:center;line-height:42px}
.quote{position:absolute;left:334px;top:12px;width:152px;height:146px;border:2px solid var(--wood-dark);background:linear-gradient(180deg,#e8a468,#d58849)}
.field{position:absolute;left:25px;width:110px;height:15px;background:var(--white);font-size:5.5px;color:#888;padding:4px 8px}
.field.area{height:34px}
.quote-btn{position:absolute;left:25px;top:119px;width:110px;height:15px;background:var(--wood-dark);border:1px solid #8c4b1d;color:var(--white);font-size:5.5px;font-weight:700;text-align:center;line-height:13px}
.knob{position:absolute;left:6px;top:56px;width:11px;height:11px;border-radius:50%;background:#eee;border:1px solid #999}

/* features */
.feature{top:304px;width:180px;text-align:center}
.badge{margin:0 auto;width:84px;height:84px;border-radius:50%;border:2px solid #b8937c;background:var(--white);line-height:80px;font-size:12px;color:#555}
.small-shelf{margin:4px auto 0;width:124px;height:6px;background:var(--wood)}
.feature p{margin-top:36px;font-size:7px;line-height:14px;color:var(--body)}
.feature .more{margin-top:10px;font-size:7.5px;color:#444}

/* why / testimonials */
.h2{font-size:11px;font-weight:600;color:#444}
.sub{font-size:5.5px;color:var(--body);margin-top:7px}
.why{left:103px;top:542px;width:234px}
.testi{left:361px;top:542px;width:253px}
.rule{height:1px;background:var(--rule);margin-top:8px}
.acc-row{display:flex;align-items:center;height:20px;border-bottom:1px solid var(--rule)}
.acc-ico{width:25px;height:20px;background:var(--accent);display:flex;align-items:center;justify-content:center}
.acc-row span{margin-left:11px;font-size:8px;font-weight:400;color:#444}
.acc-open{margin-top:11px}
.acc-body{margin-left:36px;padding:4px 0 6px;font-size:6.6px;font-weight:400;line-height:14px;color:var(--body)}
.acc-body em{display:block;font-size:6px;color:#444}
.avatar{left:463px;top:602px;width:46px;height:46px;border-radius:50%;background:linear-gradient(180deg,#e6ddd5,#c9b8aa);border:2px solid #eee}
.quote-text{left:361px;top:661px;width:253px;text-align:center;font-size:5.3px;line-height:10.5px;color:var(--body)}
.author{left:470px;top:701px;font-size:5px;font-weight:700;font-style:italic;line-height:9px;color:#444}
.dots{left:578px;top:708px;display:flex;gap:5px}
.dots i{width:8px;height:8px;border-radius:50%;border:1.5px solid #ccc;background:#eee}

/* products */
.products-head{left:103px;top:781px;width:512px;text-align:center}
.product{top:838px;width:110px;text-align:center}
.product-img{margin:0 auto;height:96px}
.product-name{margin-top:14px;font-size:6.5px;color:var(--body)}
.product-price{margin-top:5px;font-size:6.5px;color:#444}
.p-arrow{top:896px;font-size:22px;color:#555}

/* footer */
.footer{left:0;top:989px;width:720px;height:211px;background:var(--footer);color:var(--footer-text)}
.f-head{position:absolute;top:42px;font-size:8px;font-weight:700;color:var(--white)}
.f-line{position:absolute;top:63px;left:104px;width:512px;height:1px;background:#666}
.tweet{position:absolute;left:104px;width:150px;font-size:5.3px;line-height:10.5px}
.tweet b{font-size:6.5px;color:var(--white)}
.tweet small{font-size:4.5px;margin-left:28px}
.tweet-rule{position:absolute;left:104px;width:150px;height:1px;background:#666}
.thumbs{position:absolute;left:271px;top:99px;display:grid;grid-template-columns:repeat(4,30px);gap:6px}
.thumbs i{width:30px;height:30px;border:2px solid #ddd;background:linear-gradient(180deg,#9aa0a6 0 45%,#c98446 45% 70%,#e9e4dc 70%)}
.f-field{position:absolute;left:465px;width:111px;height:17px;background:var(--footer-field);border-radius:2px;font-size:5px;color:#999;padding:5px 9px}
.submit{position:absolute;left:540px;top:155px;width:36px;height:12px;background:#3d3d3d;color:var(--white);font-size:5px;font-weight:700;text-align:center;line-height:12px}
.copy{position:absolute;left:106px;top:190px;font-size:5px}
.social{position:absolute;left:520px;top:189px;display:flex;gap:8px}
.social i{width:8px;height:8px;border-radius:50%;background:#cfcfcf}
.f-bottom-line{position:absolute;left:104px;top:175px;width:512px;height:1px;background:#666}
</style>
</head>
<body>

<header>
  <div class="abs brand"><span class="brand-mark"></span><span class="brand-name">BRAMBLE OAK</span></div>
  <nav class="abs nav">
    <div class="nav-item" style="left:16px">HOME</div>
    <div class="nav-item" style="left:62px">GALLERY</div>
    <div class="nav-item" style="left:108px">SERVICE</div>
    <div class="nav-item" style="left:154px">ABOUT</div>
    <div class="nav-item" style="left:200px">CONTACT</div>
    <div class="nav-shelf"></div>
  </nav>
</header>

<section class="abs hero">
  <div class="hero-frame"></div>
  <div class="hero-photo" role="img" aria-label="Bright white kitchen with a dining table and cabinets">
    <div class="hero-arrow" style="left:0">‹</div>
    <div class="hero-arrow" style="right:0">›</div>
  </div>
  <form class="quote">
    <div class="knob"></div>
    <div class="field" style="top:8px">Your Full Name</div>
    <div class="field" style="top:30px">Your E-mail</div>
    <div class="field" style="top:52px">Your Phone Number</div>
    <div class="field area" style="top:74px">Your Discription</div>
    <div class="quote-btn">GET YOUR FREE QUOTE</div>
  </form>
  <div class="hero-top"></div>
  <div class="hero-bottom"></div>
</section>

<section>
  <div class="abs feature" style="left:76px"><div class="badge">PRODUCT</div><div class="small-shelf"></div>
    <p>Our passion is to deliver inspired cabinetry solu-<br>tions to suit all your needs, supported by our phe-<br>nomenal star class customer service</p><div class="more">Read more</div></div>
  <div class="abs feature" style="left:270px"><div class="badge">SERVICES</div><div class="small-shelf"></div>
    <p>Our passion is to deliver inspired cabinetry solu-<br>tions to suit all your needs, supported by our phe-<br>nomenal star class customer service</p><div class="more">Read more</div></div>
  <div class="abs feature" style="left:462px"><div class="badge">MISSION</div><div class="small-shelf"></div>
    <p>Our passion is to deliver inspired cabinetry solu-<br>tions to suit all your needs, supported by our phe-<br>nomenal star class customer service</p><div class="more">Read more</div></div>
</section>

<section class="abs why">
  <div class="h2">WHY CHOOSE US</div>
  <div class="sub">Vestibulum ac diam sit amet quam vehicula elementum sed sit amet dui.</div>
  <div class="rule"></div>
  <div class="acc-row acc-open" style="border:0"><div class="acc-ico"><svg width="12" height="12" viewBox="0 0 12 12"><circle cx="6" cy="6" r="5" fill="none" stroke="#fff" stroke-width="1.2"/><path d="M3.5 5l2.5 2.5L8.5 5" fill="none" stroke="#fff" stroke-width="1.2"/></svg></div><span>Quality Meterials</span></div>
  <div class="acc-body">Our passion is to deliver inspired cabinetry solutions to suit all your needs, supported by our phenomenal star class customer serviceOur passion is to deliver inspired cabinetry solutions to<em>Read more</em></div>
  <div class="acc-row" style="border-top:1px solid var(--rule)"><div class="acc-ico"><svg width="12" height="12" viewBox="0 0 12 12"><circle cx="6" cy="6" r="5" fill="none" stroke="#fff" stroke-width="1.2"/><path d="M3.5 5l2.5 2.5L8.5 5" fill="none" stroke="#fff" stroke-width="1.2"/></svg></div><span>Premium Finishes</span></div>
  <div class="acc-row"><div class="acc-ico"><svg width="12" height="12" viewBox="0 0 12 12"><circle cx="6" cy="6" r="5" fill="none" stroke="#fff" stroke-width="1.2"/><path d="M3.5 5l2.5 2.5L8.5 5" fill="none" stroke="#fff" stroke-width="1.2"/></svg></div><span>Meaningful Choices</span></div>
  <div class="acc-row"><div class="acc-ico"><svg width="12" height="12" viewBox="0 0 12 12"><circle cx="6" cy="6" r="5" fill="none" stroke="#fff" stroke-width="1.2"/><path d="M3.5 5l2.5 2.5L8.5 5" fill="none" stroke="#fff" stroke-width="1.2"/></svg></div><span>Flush Inset Doors</span></div>
</section>

<section>
  <div class="abs testi">
    <div class="h2">TESTIMONIALS</div>
    <div class="sub">Vestibulum ac diam sit amet quam vehicula elementum sed sit amet dui.</div>
    <div class="rule"></div>
  </div>
  <div class="abs avatar" role="img" aria-label="Client portrait"></div>
  <p class="abs quote-text">Vivamus magna justo, lacinia eget consectetur sed, convallis at tellus. Donec rutrum congue leo eget malesuada. Donec rutrum congue leo eget malesuada. Vestibulum ac diam sit amet quam vehicula elementum sed sit amet dui. Donec rutrum congue leo</p>
  <div class="abs author">OWEN HARTLEY<br>CEO OF NORVALE</div>
  <div class="abs dots"><i></i><i></i><i></i></div>
</section>

<section>
  <div class="abs products-head">
    <div class="h2">SOME OF OUR PRODUCTS</div>
    <div class="sub">Vestibulum ac diam sit amet quam vehicula elementum sed sit amet dui.</div>
    <div class="rule" style="margin-top:10px"></div>
  </div>
  <div class="abs p-arrow" style="left:64px">‹</div>
  <div class="abs p-arrow" style="left:646px">›</div>
  <div class="abs product" style="left:97px"><div class="product-img" role="img" aria-label="Dark wood sideboard" style="width:96px;background:linear-gradient(180deg,#fff 0 25%,#6b3a24 25%,#4a2516 78%,#fff 78%)"></div><div class="product-name">Calder-Ridge-Collection</div><div class="product-price">$598</div></div>
  <div class="abs product" style="left:205px"><div class="product-img" role="img" aria-label="Black glass-front display cabinet" style="width:58px;background:linear-gradient(180deg,#333,#1f1f1f)"></div><div class="product-name">Calder-Ridge-Collection</div><div class="product-price">$598</div></div>
  <div class="abs product" style="left:315px"><div class="product-img" role="img" aria-label="White modular cabinet boxes" style="width:96px;background:linear-gradient(180deg,#fff 0 12%,#f3f3f3 12%,#e6e6e6 88%,#fff 88%)"></div><div class="product-name">Calder-Ridge-Collection</div><div class="product-price">$598</div></div>
  <div class="abs product" style="left:418px"><div class="product-img" role="img" aria-label="Grey glass-front tall cabinet" style="width:42px;background:linear-gradient(90deg,#a3a39d,#c9cac4,#a3a39d)"></div><div class="product-name">Calder-Ridge-Collection</div><div class="product-price">$598</div></div>
  <div class="abs product" style="left:527px"><div class="product-img" role="img" aria-label="Rustic reclaimed wood armoire" style="width:80px;background:linear-gradient(90deg,#8c6a45,#a98559 50%,#8c6a45)"></div><div class="product-name">Calder-Ridge-Collection</div><div class="product-price">$598</div></div>
</section>

<footer class="abs footer">
  <div class="f-head" style="left:104px">LATEST TWEETS</div>
  <div class="f-head" style="left:270px">PHOTO GALLERY</div>
  <div class="f-head" style="left:466px">CONTACT US</div>
  <div class="f-line"></div>

  <div class="tweet" style="top:70px"><b>REID CALDER</b><small>- Posted 20-11-2015</small><br>Vestibulum ante ipsum primis in faucibus orci luctus et ultrices posuere cubilia Curae; Donec velit neque, auctor sit amet aliquam vel, ullamcorper sit amet ligula. Lorem</div>
  <div class="tweet-rule" style="top:115px"></div>
  <div class="tweet" style="top:124px"><b>REID CALDER</b><small>- Posted 20-11-2015</small><br>Vestibulum ante ipsum primis in faucibus orci luctus et ultrices posuere cubilia Curae; Donec velit neque, auctor sit amet aliquam vel, ullamcorper sit amet ligula. Lorem</div>

  <div class="tweet" style="left:270px;top:67px;width:150px">Vestibulum ante ipsum primis in faucibus orci luctus et ultrices posuere cubilia Curae; Donec velit neque, auctor</div>
  <div class="thumbs" role="img" aria-label="Gallery of finished kitchen projects"><i></i><i></i><i></i><i></i><i></i><i></i><i></i><i></i></div>

  <div class="f-field" style="top:70px">Your Full Name</div>
  <div class="f-field" style="top:93px">E-mail</div>
  <div class="f-field" style="top:114px;height:35px">Message</div>
  <div class="submit">SUBMIT</div>

  <div class="f-bottom-line"></div>
  <div class="copy">Copyright (c) at oakgrainstudio.com 2014-2015</div>
  <div class="social" aria-label="Social links"><i></i><i></i><i></i><i></i></div>
</footer>

</body>
</html>
```